Kelvo bottle Label (Yoghurt drink)

Label for a 300 ml yoghurt drink bottle in 3 flavours.

General description:
• This is to design a sleeve shrink label for a Yoghurt Drink bottle in three flavours, Classic, Strawberry and Blueberry.
• Attached 3 photos: The one with KELVO brand in the current design we want to replace using the same bottle.
• Graphically, the design is to be similar to the examples provided for drumelo and fizzcrate.
• Use font and barcode size to be readable and legal.
• Minimize the use of the upper third of the bottle as it will be distorted when the label shrinks to the bottle.
• Professional and experienced designers only are welcome, please do not waste your time otherwise.

Bottle dimensions:
• Base across: 61 mm
• Height: 145 mm (approximate)

Graphical description:
• White colour with bands at the top and bottom similar to the one in “drumelo” example provided (not necessarily identical, feel free to be creative.
• The upper and lower bands to be: Green for “classic”, Pink or red for strawberry and purple for blueberry flavour.
• On the front: the brand name “Kelvo” and description “Yoghurt Drink” to be graphically attractive.
• On the front: two or more pieces of strawberry or blueberry for each flavour placed nicely with the option to include “yoghurt splash” or any suitable affects you deem suitable.
• For the Classic flavour, use the words (Classic, Lassi, Ayran) in the same location for the berries done in a graphically suitable manner.
• Colour temperature for the three flavours to be similar.

Information and objects on the label:
Front:
• The word “Kelvo” (brand name)
• “Yoghurt drink” (Product description)
• “300 ml” (size)
• Picture of Strawberries for strawberry flavour.
• Picture of Blueberries for blueberry flavour.
• The words (Classic, Lassi, Ayran) in the place used for the strawberries in the flavoured type, distributed to look graphically suitable for the overall design.

Back:
• Ingredient: Milk/milk solids, culture, salt, water, sugar, colour, flavour. (this is to be finalized later)
• Nutrition information table: (to be provided later).
• Barcode (to be provided later)
• Product of Australia
• Morel Tunsley Pty Ltd, 5/14 Ferrit St, Malaga, WA 6090
• info@kelvo-example.com.au 0491 000 372
• Keep under 5⁰ C
• Best before date printed on the bottle
• Shake well (to be located on the side at the top)
• Recycle icon.

Health benefits: (to be located suitably, possibly on the side with vertical orientation)
• Rich in probiotic bacteria and vitamins.
• Improves digestion and bowel motion.
• Supports weight control and fat loss.

Target Market(s)

General consumers

Industry/Entity Type

Grocery Store

Font styles to use
Sans Serif

Colors
abd037
b768aa
f04a50

Requirements
Must have
• The details in the project description
• The design must be simple and neat.
• Please use the shape of the current bottle "Kelvo" as in the attached photo.
Should not have
• Busy, cluttered, or empty and incomplete designs.

```html
<!DOCTYPE html>
<html lang="en">
<head>
<meta charset="utf-8">
<title>Kelvo Strawberry Yoghurt Drink – Sleeve Label</title>
<link rel="stylesheet" href="https://fonts.googleapis.com/css2?family=Open+Sans:wght@400;600;700&family=Baloo+2:wght@800&family=Lobster&display=swap">
<style>
  :root {
    --pink: #e5087f;
    --pink-soft: #f6d3e5;
    --pink-pale: #fcecf4;
    --ink: #222222;
    --grey-fill: #e4e4e4;
    --white: #ffffff;
  }
  * { box-sizing: border-box; margin: 0; padding: 0; }
  html, body { width: 1200px; height: 505px; overflow: hidden; background: var(--white); }
  .label {
    position: relative;
    width: 1200px;
    height: 505px;
    overflow: hidden;
    font-family: "Open Sans", Arial, sans-serif;
    color: var(--ink);
  }
  .label > * { position: absolute; }

  /* Background */
  .backdrop {
    inset: 0;
    background:
      radial-gradient(ellipse 260px 200px at 60px 40px, var(--pink-soft), transparent 70%),
      radial-gradient(ellipse 240px 220px at 220px 480px, var(--pink-soft), transparent 70%),
      radial-gradient(ellipse 260px 220px at 1180px 60px, var(--pink-soft), transparent 70%),
      radial-gradient(ellipse 280px 240px at 1120px 470px, var(--pink-soft), transparent 70%),
      var(--pink-pale);
  }
  .front-panel {
    left: 436px; top: 0; width: 372px; height: 505px;
    background: var(--white);
  }
  .band-top, .band-bottom { left: 450px; width: 340px; }
  .band-top { top: 0; height: 64px; }
  .band-bottom { bottom: 0; height: 80px; }

  /* Back panel */
  .ingredients {
    left: 32px; top: 54px; width: 330px;
    font-size: 16px; line-height: 1.5;
  }
  .ingredients strong { font-weight: 700; }
  .nutrition-box {
    left: 30px; top: 189px; width: 203px; height: 257px;
    border: 1.5px solid var(--ink); background: var(--white);
  }
  .barcode-box {
    left: 239px; top: 378px; width: 185px; height: 68px;
    border: 1.5px solid var(--ink); background: var(--white);
  }
  .maker { left: 242px; top: 270px; font-size: 12.5px; line-height: 1.3; }
  .maker .origin { font-weight: 700; margin-bottom: 10px; }
  .maker .address { margin-bottom: 6px; }

  /* Front panel */
  .brand {
    left: 604px; top: 110px; width: 80px; text-align: center;
    font-weight: 700; font-size: 16px; letter-spacing: 1px; color: var(--pink);
  }
  .drops-art {
    left: 504px; top: 94px; width: 66px; height: 84px;
    border-radius: 50% 50% 45% 45%;
    background: linear-gradient(160deg, #e94e8a, #f2a33a 45%, #2fb5c4 75%, #8a3fa0);
    opacity: .85;
  }
  .product-name {
    left: 436px; top: 251px; width: 190px; height: 58px;
    transform: rotate(-90deg); transform-origin: center;
    font-family: "Baloo 2", "Arial Rounded MT Bold", sans-serif;
    font-weight: 800; font-size: 58px; line-height: 58px; text-align: center;
    color: var(--pink);
    white-space: nowrap;
  }
  .drink-word { left: 514px; top: 383px; width: 50px; text-align: center; font-size: 16px; line-height: 1; }
  .fruit-art {
    left: 584px; top: 156px; width: 216px; height: 220px;
    border-radius: 48% 52% 44% 56%;
    background: radial-gradient(circle at 45% 42%, #d8323a 0 22%, #f4c6d8 42%, #fbe6ef 62%, transparent 74%);
  }
  .flavour {
    left: 645px; top: 342px;
    font-family: "Lobster", cursive; font-size: 18px; color: var(--pink);
  }
  .volume {
    left: 666px; top: 462px; width: 100px; text-align: center;
    font-size: 24px; color: var(--white);
  }

  /* Side panel */
  .shake {
    left: 920px; top: 62px; width: 160px; text-align: center;
    font-weight: 700; font-size: 19px;
  }
  .benefits { left: 860px; top: 140px; width: 300px; height: 190px; }
  .benefit {
    position: absolute;
    display: flex; align-items: center; justify-content: center; text-align: center;
    border: 5px solid var(--pink); border-radius: 50%;
    background: linear-gradient(var(--white) 56%, var(--grey-fill) 56%);
    font-size: 10.8px; line-height: 1.4; color: var(--ink);
  }
  .benefit--probiotic { left: 20px; top: 12px; width: 94px; height: 94px; }
  .benefit--fat { left: 142px; top: 20px; width: 70px; height: 70px; font-size: 12px; }
  .benefit--weight { left: 84px; top: 96px; width: 80px; height: 80px; }
  .benefit--digestion { left: 184px; top: 80px; width: 94px; height: 94px; }
  .connectors { left: 0; top: 0; }
  .storage { left: 890px; top: 366px; font-size: 12.5px; }
  .storage sup { font-size: 8px; }
  .recycle { left: 1058px; top: 352px; }
  .best-before { left: 886px; top: 400px; font-size: 13px; }
</style>
</head>
<body>
<main class="label">
  <div class="backdrop" role="img" aria-label="Soft pink yoghurt drip pattern across the label background"></div>
  <div class="front-panel"></div>

  <svg class="band-top" viewBox="0 0 340 64" role="img" aria-label="Pink yoghurt splash band at the top of the front">
    <path d="M0 0 H340 C328 22 306 30 280 26 C258 24 244 44 222 40 C204 36 196 58 170 58 C144 58 136 38 118 42 C96 46 84 26 62 28 C36 30 12 22 0 0 Z" fill="var(--pink)"/>
  </svg>
  <svg class="band-bottom" viewBox="0 0 340 80" role="img" aria-label="Pink yoghurt splash band at the bottom of the front">
    <path d="M0 80 H340 C328 56 310 46 286 50 C266 54 254 24 230 28 C208 32 202 10 176 14 C150 18 144 38 122 34 C98 30 88 50 66 50 C38 50 14 60 0 80 Z" fill="var(--pink)"/>
  </svg>

  <!-- Back panel -->
  <p class="ingredients"><strong>INGREDIENT:</strong> Milk/milk solids, culture, salt, water, sugar, colour, flavour. (this is to be finalized later)</p>
  <div class="nutrition-box" aria-label="Nutrition information table area"></div>
  <div class="maker">
    <p class="origin">Product of Australia</p>
    <p>Morel Tunsley Pty Ltd</p>
    <p class="address">5/14 Ferrit St, Malaga, WA 6090</p>
    <p>info@kelvo-example.com.au</p>
    <p>0491 000 372</p>
  </div>
  <div class="barcode-box" aria-label="Barcode area"></div>

  <!-- Front panel -->
  <p class="brand">KELVO</p>
  <div class="drops-art" role="img" aria-label="Colourful splash droplets decoration"></div>
  <div class="fruit-art" role="img" aria-label="Strawberries falling into a pink yoghurt splash"></div>
  <p class="product-name">Yogurt</p>
  <p class="drink-word">DRINK</p>
  <p class="flavour">Strawberry</p>
  <p class="volume">300ml</p>

  <!-- Side panel -->
  <p class="shake">SHAKE WELL</p>
  <div class="benefits">
    <svg class="connectors" width="300" height="190" viewBox="0 0 300 190" aria-hidden="true">
      <g stroke="var(--pink)" stroke-width="12" stroke-linecap="round" fill="none">
        <line x1="67" y1="59" x2="124" y2="136"/>
        <line x1="177" y1="55" x2="124" y2="136"/>
        <line x1="177" y1="55" x2="231" y2="127"/>
        <line x1="67" y1="59" x2="177" y2="55"/>
      </g>
    </svg>
    <p class="benefit benefit--probiotic">Rich<br>in probiotic<br>bacteria and<br>vitamins.</p>
    <p class="benefit benefit--fat">Fat<br>loss.</p>
    <p class="benefit benefit--weight">Supports<br>Weight<br>Control</p>
    <p class="benefit benefit--digestion">Improves<br>digestion<br>and bowel<br>motion.</p>
  </div>
  <p class="storage">Keep under 5<sup>0</sup> C</p>
  <svg class="recycle" width="44" height="40" viewBox="0 0 44 40" role="img" aria-label="Recycle">
    <g fill="var(--ink)">
      <path d="M17 3 L27 3 L33 13 L37 11 L34 22 L24 20 L28 17 L23 8 L19 15 L12 11 Z"/>
      <path d="M38 22 L43 31 L38 38 L27 38 L27 42 L20 34 L27 27 L27 32 L34 32 L30 25 Z" transform="translate(0 -2)"/>
      <path d="M6 17 L11 20 L7 27 L14 27 L14 33 L4 33 L0 26 L-3 28 L0 17 Z" transform="translate(3 2)"/>
    </g>
  </svg>
  <p class="best-before">Best Before Date Printed On The Bottle</p>
</main>
</body>
</html>
```